Create Stationary from existing logo(s)

We are looking for some assistance in tidying up the stationary that supports our brand. We are an innovative technology company, generally working with larger corporates. We have previously done a little work on brochures etc, but never really pulled it all together with our stationary.
In particular I am looking for:
1. A4 Letter Template for Letter (Microsoft Word 2007 template format)
2. A4 Template for Reports (Microsoft Word 2007 template format). This should include title page, table of contents, subsequent report pages including styles for tables, headings, and text.
3. Business Card Design - we will need to be able to edit the text, so the card should include sample text for name, title, phone number, mobile number, and email address.
4. Presentation Template (Microsoft Powerpoint 2007 template). See attached powerpoint which we quite like, but isn't really a template, and we have don't really use any consistent styles in it. The Powerpoint template needs to have a cover / title page, section break pages, and pages that may contain bullet point text, pictures, or a combination of bullet point text and pictures. We do like our current presentation, which gives some indication of our thinking.
I am attaching a brochure and the powerpoint presentation to give some indication of current materials. We are happy with the main concepts behind the brochure, and would not really be looking to change the key concepts unless you have a compelling reason. We do like the use of this secondary logo in the stationary related items
I have uploaded an eps file of the logo.

```html
<!DOCTYPE html>
<html lang="en">
<head>
<meta charset="utf-8">
<title>Verano Labs – Business Cards</title>
<link href="https://fonts.googleapis.com/css2?family=Arimo:wght@400;700&display=swap" rel="stylesheet">
<style>
  :root {
    --page-bg: #ffffff;
    --card-light: #ffffff;
    --card-dark: #1a4c7c;
    --card-edge: #555555;
    --ink-strong: #555555;
    --ink-on-dark: #ffffff;
    --brand-orange: #f08a1c;
    --brand-navy: #233e7a;
    --accent-pale: #d6e8f7;
    --accent-mid: #8cc0ea;
    --accent-deep: #4796dc;
  }
  * { box-sizing: border-box; margin: 0; padding: 0; }
  html, body {
    width: 1200px; height: 1146px; overflow: hidden;
    background: var(--page-bg);
    font-family: "Arimo", Arial, sans-serif;
  }
  .sheet { position: relative; width: 1200px; height: 1146px; }
  .card {
    position: absolute; top: 190px;
    width: 420px; height: 714px;
    border-radius: 33px; overflow: hidden;
  }
  .card--light { left: 132px; background: var(--card-light); border: 1.5px solid var(--card-edge); color: var(--ink-strong); }
  .card--dark { left: 673px; background: var(--card-dark); color: var(--ink-on-dark); }
  .card__art { position: absolute; inset: 0; width: 100%; height: 100%; }
  .brand {
    position: absolute; left: 40px; top: 64px;
    display: flex; align-items: center; gap: 12px;
    font-weight: 700; font-size: 31px; letter-spacing: -0.5px;
    color: var(--brand-orange);
  }
  .brand__mark { width: 30px; height: 30px; background: var(--brand-navy); }
  .card--dark .brand__mark { background: var(--ink-on-dark); }
  .details { position: absolute; left: 28.5px; top: 203px; }
  .person__name { font-size: 24px; font-weight: 700; line-height: 30px; }
  .person__role { font-size: 21px; line-height: 28px; }
  .contact { margin-top: 58px; font-size: 21px; line-height: 28px; }
  .contact b { font-weight: 700; }
  .web { margin-top: 32px; font-size: 21px; line-height: 24px; }
  .address { margin-top: 34px; font-size: 18px; line-height: 25px; }
</style>
</head>
<body>
<main class="sheet">

  <section class="card card--light">
    <svg class="card__art" viewBox="0 0 420 714">
      <defs>
        <linearGradient id="accent-light" x1="0" y1="0" x2="1" y2="0">
          <stop offset="0" stop-color="var(--accent-pale)" stop-opacity="0.4"/>
          <stop offset="0.6" stop-color="var(--accent-mid)" stop-opacity="0.8"/>
          <stop offset="1" stop-color="var(--accent-deep)"/>
        </linearGradient>
      </defs>
      <path role="img" aria-label="Decorative area: flowing blue line waves with soft orange dots along the right edge"
            d="M350 0 L420 0 L420 714 L290 714 Z" fill="url(#accent-light)"/>
    </svg>
    <div class="brand"><span class="brand__mark"></span>Verano Labs</div>
    <div class="details">
      <p class="person__name">Jordan Hale</p>
      <p class="person__role">Brand Manager</p>
      <p class="contact"><b>P:</b> +61 2 9410 5276<br><b>F:</b> +61 2 8155 3609</p>
      <p class="web">hello@veranolabs.com.au<br>www.veranolabs.com.au</p>
      <p class="address">Level 6, 120 Keel Street<br>Marlow, 2100<br>Australia</p>
    </div>
  </section>

  <section class="card card--dark">
    <svg class="card__art" viewBox="0 0 420 714">
      <defs>
        <linearGradient id="accent-dark" x1="0" y1="0" x2="1" y2="0">
          <stop offset="0" stop-color="var(--accent-pale)" stop-opacity="0.1"/>
          <stop offset="0.6" stop-color="var(--accent-mid)" stop-opacity="0.55"/>
          <stop offset="1" stop-color="var(--accent-deep)"/>
        </linearGradient>
      </defs>
      <path role="img" aria-label="Decorative area: flowing blue line waves with soft slate dots along the right edge"
            d="M350 0 L420 0 L420 714 L290 714 Z" fill="url(#accent-dark)"/>
    </svg>
    <div class="brand"><span class="brand__mark"></span>Verano Labs</div>
    <div class="details">
      <p class="person__name">Jordan Hale</p>
      <p class="person__role">Brand Manager</p>
      <p class="contact"><b>P:</b> +61 2 9410 5276<br><b>F:</b> +61 2 8155 3609</p>
      <p class="web">hello@veranolabs.com.au<br>www.veranolabs.com.au</p>
      <p class="address">Level 6, 120 Keel Street<br>Marlow, 2100<br>Australia</p>
    </div>
  </section>

</main>
</body>
</html>
```